Last of Tides

Story is a sequel to "Dusk of Copper Rain" which was a trip of an old ship with that name to India at the end of the Flower Power Era. This story is the aftermath of its eventual end in the scrapyard of Formosa. It describes the rather wild return trip of the motley crew from India via |Formosa back to the US with the dramatic undertone that the maritime industry is changing from the traditional break-bulk cargo transport to the modern method of container transport. The plot also involves a heist of thousands of bottles of whisky but that is of lesser concern. Design should be simple, be in the same style (with the original design of a single wilting flower on a beach) to affect its relation to the first book.The last of tides really signiies the end of traditional break-bulk (piecemeal) cargoship transport that had been done for thousands of years.

Target Market(s)

Young Adults and anyone associated with the Maritime Industry

Industry/Entity Type

Maritime industry

Font styles to use
Serif
Sans Serif
Other font styles liked:
• Arial or similar for the title; Serif for Author's name and text on back

Requirements
Must have
• Association with the first book design. Simple but effective design; subdued color scheme
Nice to have
• Totally wilted flower(s); deserted beach; sinking (dargo) ship (1960's); Sea;
Should not have
• Faces and pictures of personns, no complicated designs with lots of detail reflecting the plot; no bright colors

```html
<!DOCTYPE html>
<html lang="en">
<head>
<meta charset="utf-8">
<title>Last of Tides — Book Cover</title>
<link rel="stylesheet" href="https://fonts.googleapis.com/css2?family=Marcellus&family=Cormorant+Garamond:ital,wght@1,500&display=swap">
<style>
  :root {
    --backdrop: #262626;
    --ink: #0b0b0b;
    --sky-top: #eceeea;
    --sky-low: #dde7e6;
    --sea: #c9dbd6;
    --foam: #f4f5f3;
    --sand-light: #ddd0b6;
    --sand: #d3c19f;
  }
  html, body {
    margin: 0;
    width: 1200px;
    height: 1200px;
    overflow: hidden;
    background: var(--backdrop);
  }
  .cover {
    position: absolute;
    left: 224px;
    top: 35px;
    width: 753px;
    height: 1129px;
    overflow: hidden;
  }
  .cover-photo {
    position: absolute;
    inset: 0;
    background: linear-gradient(to bottom,
      var(--sky-top) 0%,
      var(--sky-low) 60%,
      var(--sea) 61.5%,
      var(--sea) 63.5%,
      var(--foam) 67%,
      var(--foam) 76%,
      #e8e6dc 78.5%,
      var(--sand-light) 80%,
      var(--sand) 100%);
  }
  .cover-type {
    position: absolute;
    inset: 0;
  }
  .title-word {
    font-family: "Marcellus", serif;
    font-size: 168px;
    letter-spacing: 0.07em;
    fill: var(--ink);
  }
  .title-joiner {
    font-family: "Cormorant Garamond", serif;
    font-style: italic;
    font-weight: 500;
    font-size: 96px;
    fill: var(--ink);
  }
  .author {
    font-family: "Marcellus", serif;
    font-size: 30px;
    letter-spacing: 0.12em;
    fill: var(--ink);
  }
</style>
</head>
<body>
  <article class="cover">
    <div class="cover-photo" role="img" aria-label="Photograph of a deserted beach: pale misty sky, calm sea with white surf, and sand in the foreground with a single totally wilted dried flower lying on it"></div>
    <svg class="cover-type" width="753" height="1129" viewBox="0 0 753 1129">
      <text class="title-word" x="380" y="231" text-anchor="middle">LAST</text>
      <text class="title-joiner" x="378" y="369" text-anchor="middle">of</text>
      <text class="title-word" x="380" y="574" text-anchor="middle">TIDES</text>
      <text class="author" x="380" y="1070" text-anchor="middle">WIM HARKEMA</text>
    </svg>
  </article>
</body>
</html>
```